Harbor Crestline (Business Card Design)

Need business cards designed. Something modern, chic, and sleek. Mabye the back of the card should be the navy blue that is in the logo and then just the logo on the back.

Target Market(s)

Those in the hotel, office, and renovation industry

Contact Information for Business Card

1. Logo 2. Dorian Fenwick 3. CEO/Founder 4. Phone: (833) HarbCre / (833) 427-2731 5. Email: dorian@theharborcrestline.com 6. Website: www.theharborcrestline.com

Font styles to use
Other font styles liked:
• Look at the logo font and base the font for everything else off of that.

Colors
0054AA
0677BA
7BADD7
CADEEF
E8F1F8

Requirements
Must have
• Colors that are associated in the logo
Nice to have
• Sleek modern clean and chic design.

```html
<!DOCTYPE html>
<html lang="en">
<head>
<meta charset="utf-8">
<title>Harbor Crestline – Business Cards</title>
<link href="https://fonts.googleapis.com/css2?family=Montserrat:wght@500;600;700&family=Open+Sans:wght@400;600&display=swap" rel="stylesheet">
<style>
  :root {
    --stage: #232323;
    --navy: #0e1a42;
    --navy-light: #1b2a5e;
    --navy-deep: #0a1333;
    --gold: #c9a545;
    --white: #ffffff;
    --rule: rgba(255,255,255,0.85);
  }
  * { box-sizing: border-box; margin: 0; padding: 0; }
  html, body {
    width: 1200px; height: 780px; overflow: hidden;
    background: var(--stage);
  }
  .canvas { position: relative; width: 1200px; height: 780px; }

  .card {
    position: absolute;
    width: 540px; height: 309px;
    background: var(--navy);
    border-radius: 3px;
    box-shadow: 0 14px 30px rgba(0,0,0,0.55);
    overflow: hidden;
  }
  .card--front { left: 60px; top: 50px; }
  .card--back  { left: 600px; top: 420px; }

  /* Front */
  .front-pattern {
    position: absolute; inset: 0;
    background: linear-gradient(200deg, #5d5f9a 0%, var(--navy-light) 35%, var(--navy) 60%, var(--navy-deep) 100%);
    opacity: 0.9;
  }
  .front-lockup {
    position: absolute; left: 0; right: 0; top: 50%;
    transform: translateY(-50%);
    display: flex; align-items: center; justify-content: center; gap: 16px;
  }
  .brand-mark {
    width: 18px; height: 18px; background: var(--gold);
  }
  .brand-name {
    font-family: "Montserrat", sans-serif;
    font-weight: 600;
    color: var(--white);
    letter-spacing: 0.14em;
    text-transform: uppercase;
    white-space: nowrap;
  }
  .front-lockup .brand-name { font-size: 30px; }

  /* Back */
  .back-lockup {
    position: absolute; left: 34px; top: 46px;
    display: flex; align-items: center; gap: 10px;
  }
  .back-lockup .brand-mark { width: 12px; height: 12px; }
  .back-lockup .brand-name { font-size: 17px; }

  .holder {
    position: absolute; right: 46px; top: 42px; text-align: right;
  }
  .holder-name {
    font-family: "Montserrat", sans-serif; font-weight: 700;
    font-size: 26px; line-height: 1.1; white-space: nowrap;
  }
  .holder-name .first { color: var(--gold); }
  .holder-name .last { color: var(--white); }
  .holder-title {
    font-family: "Open Sans", sans-serif; font-weight: 600;
    font-size: 13px; color: var(--white); margin-top: 3px;
  }
  .holder-bar {
    position: absolute; right: 0; top: 42px;
    width: 22px; height: 48px; background: var(--gold);
  }
  .divider {
    position: absolute; left: 34px; right: 34px; top: 130px;
    height: 1px; background: var(--rule);
  }
  .contact {
    position: absolute; left: 40px; top: 148px;
    font-family: "Open Sans", sans-serif; color: var(--white);
    font-size: 13px; line-height: 1.45;
  }
  .address { margin-bottom: 14px; }
  .contact-list { list-style: none; }
  .contact-list li { display: flex; align-items: center; gap: 9px; }
  .contact-icon { width: 12px; height: 12px; flex: none; }
</style>
</head>
<body>
<main class="canvas">

  <section class="card card--front" aria-label="Business card front">
    <div class="front-pattern" role="img" aria-label="Repeating brand pattern fading from light to dark navy"></div>
    <div class="front-lockup">
      <span class="brand-mark"></span>
      <span class="brand-name">Harbor Crestline</span>
    </div>
  </section>

  <section class="card card--back" aria-label="Business card back">
    <div class="back-lockup">
      <span class="brand-mark"></span>
      <span class="brand-name">Harbor Crestline</span>
    </div>

    <div class="holder">
      <p class="holder-name"><span class="first">Dorian</span> <span class="last">Fenwick</span></p>
      <p class="holder-title">CEO/Founder</p>
    </div>
    <span class="holder-bar"></span>

    <span class="divider"></span>

    <div class="contact">
      <p class="address">4120 Merrow Lane<br>Suite 2100, Aldergrove, MD 21390</p>
      <ul class="contact-list">
        <li>
          <svg class="contact-icon" viewBox="0 0 24 24" aria-hidden="true"><path fill="#c9a545" d="M6.6 10.8a15.1 15.1 0 0 0 6.6 6.6l2.2-2.2a1 1 0 0 1 1-.25 11.4 11.4 0 0 0 3.6.57 1 1 0 0 1 1 1V20a1 1 0 0 1-1 1A17 17 0 0 1 3 4a1 1 0 0 1 1-1h3.5a1 1 0 0 1 1 1c0 1.25.2 2.45.57 3.57a1 1 0 0 1-.25 1z"/></svg>
          (833) HarbCre / (833) 427-2731
        </li>
        <li>
          <svg class="contact-icon" viewBox="0 0 24 24" aria-hidden="true"><g fill="none" stroke="#c9a545" stroke-width="2.2"><circle cx="12" cy="12" r="9.5"/><ellipse cx="12" cy="12" rx="4" ry="9.5"/><path d="M2.5 12h19"/></g></svg>
          www.theharborcrestline.com
        </li>
        <li>
          <svg class="contact-icon" viewBox="0 0 24 24" aria-hidden="true"><g fill="none" stroke="#c9a545" stroke-width="2.2"><rect x="2.5" y="5" width="19" height="14" rx="1"/><path d="M2.5 6l9.5 7 9.5-7"/></g></svg>
          dorian@theharborcrestline.com
        </li>
      </ul>
    </div>
  </section>

</main>
</body>
</html>
```